Harborline Auto LLC

Car Dealer Customer Service
Address: 2874 Cresthaven Road, Shelbyville, TN 37162
web: www.harborlineautoxq.net
email: harborlineautoxq@mailnest.example
Phone: (931) 555-0148
Phone: (629) 555-0173

```html
<!DOCTYPE html>
<html lang="en">
<head>
<meta charset="utf-8">
<title>Harborline Auto — Business Card</title>
<link rel="stylesheet" href="https://fonts.googleapis.com/css2?family=Poppins:wght@400;500;600;700&display=swap">
<style>
  :root {
    --stage: #2f2f2f;
    --paper: #ffffff;
    --navy: #2e2a7d;
    --gold: #f0ad35;
    --ink: #111111;
    --rule: #8a8a8a;
  }
  * { margin: 0; padding: 0; box-sizing: border-box; }
  html, body { width: 1200px; height: 979px; overflow: hidden; }
  body {
    background: var(--stage);
    font-family: "Poppins", sans-serif;
    position: relative;
  }
  .card {
    position: absolute;
    width: 520px;
    height: 297px;
    box-shadow: 0 10px 28px rgba(0,0,0,0.35);
  }
  /* Front */
  .card--front { left: 120px; top: 150px; background: var(--paper); }
  .brand {
    position: absolute;
    left: 62px; top: 128px;
    display: flex; align-items: center; gap: 10px;
  }
  .brand__dot { width: 30px; height: 30px; border-radius: 50%; background: var(--gold); }
  .brand__name {
    color: var(--navy);
    font-weight: 700;
    font-size: 16px;
    line-height: 1;
    letter-spacing: 0.2px;
  }
  .divider {
    position: absolute;
    left: 274px; top: 88px;
    width: 1.5px; height: 122px;
    background: var(--rule);
  }
  .person { position: absolute; left: 301px; top: 97px; color: var(--ink); }
  .person__name { font-size: 17px; font-weight: 500; letter-spacing: 0.3px; line-height: 1.1; }
  .person__name strong { font-weight: 700; }
  .person__role { font-size: 12px; color: #333; margin-top: 1px; }
  .contacts {
    position: absolute; left: 301px; top: 156px;
    list-style: none; font-size: 8.4px; color: var(--ink);
  }
  .contacts li { display: flex; align-items: center; gap: 6px; height: 14.5px; }
  .contacts svg { width: 9px; height: 9px; flex: none; }

  /* Back */
  .card--back { left: 560px; top: 530px; background: var(--navy); color: var(--paper); text-align: center; }
  .back__dot {
    position: absolute; left: 50%; top: 66px;
    width: 96px; height: 96px; margin-left: -48px;
    border-radius: 50%; background: var(--gold);
  }
  .back__name {
    position: absolute; left: 0; right: 0; top: 184px;
    font-size: 22px; font-weight: 700; letter-spacing: 0.6px; line-height: 1;
  }
  .back__tagline {
    position: absolute; left: 0; right: 0; top: 212px;
    font-size: 9px; font-weight: 600; letter-spacing: 0.4px;
  }
</style>
</head>
<body>
  <section class="card card--front">
    <div class="brand">
      <span class="brand__dot"></span>
      <span class="brand__name">HARBORLINE<br>AUTO</span>
    </div>
    <div class="divider"></div>
    <div class="person">
      <p class="person__name">PERSON <strong>NAME</strong></p>
      <p class="person__role">President</p>
    </div>
    <ul class="contacts">
      <li>
        <svg viewBox="0 0 10 10" fill="none" stroke="#111" stroke-width="0.9"><circle cx="5" cy="5" r="4.2"/><ellipse cx="5" cy="5" rx="1.8" ry="4.2"/><path d="M0.8 5h8.4M1.5 3h7M1.5 7h7"/></svg>
        www.harborlineautoxq.net
      </li>
      <li>
        <svg viewBox="0 0 10 10"><rect x="0.5" y="2" width="9" height="6" fill="#111"/><path d="M0.8 2.3L5 5.6 9.2 2.3" fill="none" stroke="#fff" stroke-width="0.8"/></svg>
        harborlineautoxq@mailnest.example
      </li>
      <li>
        <svg viewBox="0 0 10 10"><path d="M2.2 0.8l1.6 2.2-1 1c.6 1.3 1.6 2.3 2.9 2.9l1-1 2.2 1.6-1 1.8C4.4 9.4.6 5.6.4 1.8z" fill="#111"/></svg>
        (931) 555-0148, (629) 555-0173
      </li>
    </ul>
  </section>

  <section class="card card--back">
    <span class="back__dot"></span>
    <h1 class="back__name">HARBORLINE AUTO</h1>
    <p class="back__tagline">CAR DEALER CUSTOMER SERVICE</p>
  </section>
</body>
</html>
```